brovlanepass.net

Develop a website for brolanepass.net will be a site to sell tickets for concerts, shows, shows, theaters and others. I need a web design easy view, very easy to use and accumulate events by date. The aim is to develop the site was connected to a complex system that is already developed. (Important this page to a robust system was connected via links the idea is to develop only the front view)
Updates

Reason: I need more designs yet we have not made the decision

Target Market(s)

millennials, adults, who want to enjoy concerts and shows

Industry/Entity Type

Event

Number of Pages Required

5+ page

Colors
1b1b1b
aaaaaa
ffffff

Requirements
Must have
• Easy Vista, accumulation of upcoming events, past events. The tabs should have are: 1 Start: In this part of upcoming events occur. You could put a banner on the top and down the events by date. 2. How to order: page with instructions on how to purchase tickets 3. About Us: The company history 4. Contact: Phones and template for contact by mail 5. Our policies: shopping 6. Notice Privacy: Privacy Notice Copoy 7. Centers Sale: physical places where they can purchase tickets Promoters 8. access: Link to a template
Nice to have
• as you can see p www.quimbarostage.net or farunda.net or farunda.org or gallowmerk.net (important this page to a robust system was connected via links the idea is to develop only the front view)
Should not have
• Many things Tangled

```html
<!DOCTYPE html>
<html lang="en">
<head>
<meta charset="utf-8">
<title>Brovlane Pass — About Us</title>
<link href="https://fonts.googleapis.com/css2?family=Nunito:wght@800;900&family=Open+Sans:wght@400;600&display=swap" rel="stylesheet">
<style>
  :root {
    --ink: #ffffff;
    --text-soft: #d6d0d6;
    --header-bg: #050505;
    --nav-bg: #1b1b1b;
    --accent: #e24b4b;
    --page-bg: #1c1219;
    --about-bg: #2a1726;
    --mission-bg: #1e141d;
    --values-bg: #2b1322;
    --footer-bg: #171214;
    --rule: #4a3d47;
    --muted: #aaaaaa;
  }
  * { margin: 0; padding: 0; box-sizing: border-box; }
  html, body { width: 886px; height: 1200px; overflow: hidden; }
  body {
    position: relative;
    background: var(--page-bg);
    color: var(--ink);
    font-family: "Open Sans", Arial, sans-serif;
  }
  .abs { position: absolute; }

  /* Header */
  .site-header { left: 0; top: 0; width: 886px; height: 83px; background: var(--header-bg); }
  .phone-badge { left: 77px; top: 26px; width: 32px; height: 32px; border: 1.5px solid var(--ink); border-radius: 50%; }
  .phone-badge svg { position: absolute; left: 8px; top: 8px; }
  .phone-number { left: 118px; top: 29px; font-size: 17px; letter-spacing: 0.2px; }
  .brand { display: flex; align-items: center; gap: 6px; font-weight: 600; font-size: 14px; letter-spacing: 0.6px; color: var(--ink); }
  .brand-mark { width: 13px; height: 13px; background: var(--accent); flex: none; }
  .header-brand { left: 374px; top: 32px; }
  .social-row { display: flex; gap: 10px; }
  .social-row span { width: 18px; height: 18px; border-radius: 3px; display: block; }
  .header-social { left: 712px; top: 32px; }
  .header-social span { background: #2b8fd6; }
  .header-social span:last-child { background: var(--accent); }

  /* Navigation */
  .main-nav { left: 0; top: 83px; width: 886px; height: 42px; background: linear-gradient(#1f1f1f, #121212); }
  .main-nav a { position: absolute; top: 14px; font-size: 12.5px; color: var(--ink); text-decoration: none; letter-spacing: 0.2px; }
  .main-nav .active { top: 0; height: 42px; padding-top: 14px; border-top: 3px solid var(--accent); background: #101010; width: 84px; text-align: center; }

  /* Hero */
  .page-hero { left: 0; top: 125px; width: 886px; height: 133px;
    background: radial-gradient(ellipse at 75% 40%, #5a5560 0%, #2c2a30 35%, #121114 80%); }
  .page-hero h1 { position: absolute; left: 0; top: 57px; width: 886px; text-align: center;
    font-family: "Nunito", Arial, sans-serif; font-weight: 900; font-size: 27px; letter-spacing: 0.4px; }

  /* About */
  .about-section { left: 0; top: 258px; width: 886px; height: 294px;
    background: radial-gradient(ellipse at 30% 100%, #4a1f38 0%, var(--about-bg) 45%, #1f1420 100%); }
  .about-photo { left: 66px; top: 50px; width: 301px; height: 200px;
    background: radial-gradient(circle at 30% 25%, #6fb6d8 0%, #2c5a84 30%, #0e1a30 75%); }
  .section-title { font-weight: 400; font-size: 23px; letter-spacing: 0.3px; }
  .about-copy { left: 390px; top: 54px; width: 432px; }
  .body-text { font-size: 10.6px; line-height: 16.8px; letter-spacing: -0.15px; color: var(--text-soft); text-align: justify; hyphens: auto; }
  .about-copy .body-text { margin-top: 6px; }

  /* Mission & View */
  .purpose-section { left: 0; top: 552px; width: 886px; height: 234px; background: var(--mission-bg); }
  .purpose-divider { left: 443px; top: 24px; width: 1px; height: 188px; background: var(--rule); }
  .purpose-col { top: 40px; width: 341px; }
  .purpose-col h3 { font-weight: 400; font-size: 15.5px; margin: 4px 0 5px; }
  .mission { left: 67px; }
  .view { left: 484px; top: 39px; }

  /* Values */
  .values-section { left: 0; top: 786px; width: 886px; height: 199px;
    background: radial-gradient(ellipse at 50% 60%, #4a1a34 0%, var(--values-bg) 50%, #1f1219 100%); }
  .values-section h2 { position: absolute; left: 0; top: 42px; width: 886px; text-align: center; }
  .values-section p { position: absolute; left: 92px; top: 84px; width: 702px; text-align: center; color: var(--text-soft); }

  /* Footer */
  .site-footer { left: 0; top: 985px; width: 886px; height: 215px; background: var(--footer-bg); }
  .footer-brand { left: 66px; top: 89px; }
  .footer-col { top: 44px; }
  .footer-col h4 { font-weight: 400; font-size: 12px; letter-spacing: 0.2px; margin-bottom: 14px; }
  .contact-list { list-style: none; font-size: 10px; line-height: 16.2px; }
  .contact-col { left: 253px; }
  .mailing-col { left: 474px; }
  .mailing-col p { font-size: 8.5px; line-height: 12px; width: 150px; margin-top: -3px; }
  .signup { display: flex; margin-top: 9px; }
  .signup span { display: block; height: 23px; font-size: 8.5px; line-height: 23px; }
  .signup .field { width: 108px; background: #ffffff; color: #8a8a8a; padding-left: 6px; }
  .signup .submit { width: 41px; background: #4a4a4a; color: var(--ink); text-align: center; }
  .follow-col { left: 695px; }
  .footer-social { margin-top: 18px; }
  .footer-social span { background: var(--ink); }
  .footer-rule { left: 56px; top: 166px; width: 755px; height: 1px; background: var(--rule); }
  .copyright { left: 0; top: 184px; width: 886px; text-align: center; font-size: 9.5px; }
</style>
</head>
<body>

<header class="site-header abs">
  <div class="phone-badge abs">
    <svg width="14" height="14" viewBox="0 0 24 24" fill="#ffffff" aria-hidden="true">
      <path d="M6.6 10.8a15.2 15.2 0 0 0 6.6 6.6l2.2-2.2c.3-.3.7-.4 1-.2 1.1.4 2.3.6 3.6.6.6 0 1 .4 1 1V20c0 .6-.4 1-1 1A17 17 0 0 1 3 4c0-.6.4-1 1-1h3.5c.6 0 1 .4 1 1 0 1.3.2 2.5.6 3.6.1.3 0 .7-.2 1l-2.3 2.2z"/>
    </svg>
  </div>
  <div class="phone-number abs">+852 5100 4827</div>
  <div class="brand header-brand abs"><span class="brand-mark"></span>BROVLANE PASS</div>
  <div class="social-row header-social abs"><span></span><span></span><span></span><span></span></div>
</header>

<nav class="main-nav abs">
  <a href="#" style="left:90px">HOME</a>
  <a href="#" style="left:161px">HOW TO ORDER</a>
  <a href="#" class="active" style="left:272px">ABOUT US</a>
  <a href="#" style="left:378px">CONTACT US</a>
  <a href="#" style="left:485px">POLICIES</a>
  <a href="#" style="left:570px">PRIVACY</a>
  <a href="#" style="left:652px">CENTER SALE</a>
  <a href="#" style="left:760px">ACCESS</a>
</nav>

<section class="page-hero abs" role="img" aria-label="Concert hall audience facing a lit stage">
  <h1>ABOUT US</h1>
</section>

<section class="about-section abs">
  <div class="about-photo abs" role="img" aria-label="Rock band performing on stage under blue spotlights"></div>
  <div class="about-copy abs">
    <h2 class="section-title">ABOUT US</h2>
    <p class="body-text">It is a long established fact that a reader will be distracted by the readable content of a page when looking at its layout. The point of using Lorem Ipsum is that it has a more-or-less normal distribution of letters, as opposed to using 'Content here, content here', making it look like readable English. Many desktop publishing packages and web page editors now use Lorem Ipsum as their default model text, and a search for 'lorem ipsum' will uncover many web sites still in their infancy. Various versions have evolved over the years, sometimes by accident, sometimes on purpose It is a long established fact that a reader will be distracted by the readable content of a page when looking at its layout. The point of using Lorem Ipsum is that it has a more-or-less normal distribution.</p>
  </div>
</section>

<section class="purpose-section abs">
  <div class="purpose-col mission abs">
    <h2 class="section-title">MISSION</h2>
    <h3>Why are we here?</h3>
    <p class="body-text">It is a long established fact that a reader will be distracted by the read&shy;able content of a page when looking at its layout. The point of using Lorem Ipsum is that it has a more-or-less normal distribution of letters, as opposed to using 'Content here, content here', making it look like readable English. Many desktop publishing packages and web page</p>
  </div>
  <div class="purpose-divider abs"></div>
  <div class="purpose-col view abs">
    <h2 class="section-title">VIEW</h2>
    <h3>Where are we going?</h3>
    <p class="body-text">It has survived not only five centuries, but also the leap into electronic typesetting, remaining essentially unchanged. It was popularised in the 1960s with the release of Varnley sheets containing Lorem Ipsum pas&shy;sages, and more recently with desktop publishing software like Quillmark Pagesetter including versions of Lorem Ipsum.</p>
  </div>
</section>

<section class="values-section abs">
  <h2 class="section-title">VALUES</h2>
  <p class="body-text">It is a long established fact that a reader will be distracted by the readable content of a page when looking at its layout. The point of using Lorem Ipsum is that it has a more-or-less normal distribution of letters, as opposed to using 'Content here, content here', making it look like readable English. Many desktop publishing packages and web page editors now use Lorem Ipsum as their default model text, and a search for 'lorem ipsum' will uncover many web sites still in their infancy. Various versions have evolved over the years, sometimes by accident,</p>
</section>

<footer class="site-footer abs">
  <div class="brand footer-brand abs"><span class="brand-mark"></span>BROVLANE PASS</div>
  <div class="footer-col contact-col abs">
    <h4>CONTACT US</h4>
    <ul class="contact-list">
      <li>Address : 2716 Calloway Ln,</li>
      <li>Brindlemoor, Fl, 33914</li>
      <li>Phone : 508-555-0142</li>
      <li>Email : info@brovlanepass.net</li>
    </ul>
  </div>
  <div class="footer-col mailing-col abs">
    <h4>JOIN OUR MAILING LIST</h4>
    <p>Your about us information would fit here nicely.</p>
    <div class="signup"><span class="field">Email address</span><span class="submit">Submit</span></div>
  </div>
  <div class="footer-col follow-col abs">
    <h4>FOLLOW US OUT THERE</h4>
    <div class="social-row footer-social"><span></span><span></span><span></span><span></span></div>
  </div>
  <div class="footer-rule abs"></div>
  <div class="copyright abs">Copyright © 2017. All Rights Reserved</div>
</footer>

</body>
</html>
```